Business Cards Design for the electrical wholesaler: clean bold dynamic :)

We need a business card design that would follow our latest brand guidelines. As an electrical wholesaler we want to bring a fresh look and feel into the industry. The design should be clean bold and dynamic. It should come alive with the renewed energy of our green colour. Our grey colour should keep things balanced and complement the notion of maturity and responsibility. We employ Lato as a corporate font however are not bound by this font and we’re open to interpretation here.

Target Market(s)

Electrical contractors

Industry/Entity Type

Business

Contact Information for Business Card

Logo
Name & Surname: Halyna Dorosh
Job Title: Director of Marketing
Email: halya.dorosh@quillmail.example
Cell phone: XXX.XXX.XXXX
Address: 20517 - 87 Ave. Edmonton, AB, Canada. T6K 4N8
Business Phone: 780.555.0184
Website: www.brovix.example

Font styles to use
Other font styles liked:
• Lato

Requirements
Must have
• Logo & website
Nice to have
• Brand elements - some of them you may find in the attached Brand Guidelines (e.g. three lines on the background signifying "W")

```html
<!DOCTYPE html>
<html lang="en">
<head>
<meta charset="utf-8">
<title>Brovix Business Card</title>
<link rel="stylesheet" href="https://fonts.googleapis.com/css2?family=Lato:wght@400;700&display=swap">
<style>
  :root {
    --backdrop: #2b2b2c;
    --card-light: #f3f3f2;
    --card-dark: #4c4d4f;
    --band-grey: #4a4b4d;
    --brand-green: #8cc63e;
    --text-grey: #555658;
    --white: #ffffff;
  }
  * { margin: 0; padding: 0; box-sizing: border-box; }
  html, body { width: 1200px; height: 960px; overflow: hidden; }
  body {
    position: relative;
    background: var(--backdrop);
    font-family: "Lato", Arial, sans-serif;
    color: var(--text-grey);
  }
  .card {
    position: absolute;
    width: 600px;
    height: 342px;
    border-radius: 22px;
    overflow: hidden;
  }
  .card-front { left: 314px; top: 113px; background: var(--card-light); }
  .card-back { left: 311px; top: 472px; background: var(--card-dark); height: 341px; }

  .name-band {
    position: absolute;
    left: 0; top: 53px;
    width: 300px; height: 56px;
    background: var(--band-grey);
    padding: 7px 0 0 43px;
  }
  .person-name {
    color: var(--brand-green);
    font-weight: 700;
    font-size: 21px;
    line-height: 24px;
  }
  .person-title {
    color: var(--white);
    font-size: 16px;
    line-height: 19px;
  }

  .brand {
    position: absolute;
    display: flex;
    align-items: center;
    gap: 12px;
  }
  .brand-mark { width: 26px; height: 26px; background: var(--brand-green); }
  .brand-name { font-weight: 700; letter-spacing: 0.5px; line-height: 1; }
  .card-front .brand { right: 44px; top: 57px; }
  .card-front .brand-name { font-size: 48px; color: var(--band-grey); }
  .card-back .brand { left: 50%; top: 128px; transform: translateX(-50%); gap: 16px; }
  .card-back .brand-mark { width: 36px; height: 36px; }
  .card-back .brand-name { font-size: 66px; color: var(--white); }

  .contact-list {
    position: absolute;
    left: 46px; top: 227px;
    list-style: none;
    font-size: 14.5px;
    line-height: 19px;
  }
  .contact-list li { display: flex; align-items: center; gap: 8px; }
  .contact-list svg { width: 14px; height: 14px; fill: var(--brand-green); flex: none; }

  .address-block {
    position: absolute;
    right: 44px; top: 246px;
    text-align: right;
    font-size: 14.5px;
    line-height: 19.5px;
  }
  .address-block .web { margin-top: 1px; }

  .back-web {
    position: absolute;
    left: 0; right: 0; top: 292px;
    text-align: center;
    color: var(--white);
    font-size: 14px;
    letter-spacing: 3.4px;
  }
</style>
</head>
<body>
  <section class="card card-front" aria-label="Business card front">
    <div class="name-band">
      <div class="person-name">HALYNA DOROSH</div>
      <div class="person-title">CEO/FOUNDER</div>
    </div>

    <div class="brand">
      <span class="brand-mark"></span>
      <span class="brand-name">brovix</span>
    </div>

    <ul class="contact-list">
      <li>
        <svg viewBox="0 0 16 16" aria-hidden="true"><path d="M3.6 1.2l2.2 2.6-1.3 1.6c.9 2 2.4 3.6 4.3 4.6l1.6-1.3 2.6 2.2-1.1 2.6C7 13.1 2.9 9 1 4.1z"/></svg>
        <span>780.555.0184</span>
      </li>
      <li>
        <svg viewBox="0 0 16 16" aria-hidden="true"><path d="M4.5 1h7v14h-7zM6 2.6v9.2h4V2.6zM7.3 12.6h1.4v1.2H7.3z" fill-rule="evenodd"/></svg>
        <span>780.555.0127</span>
      </li>
      <li>
        <svg viewBox="0 0 16 16" aria-hidden="true"><path d="M4 1h7l1 1v3H4zM1 6h14v6h-2.5v-2h-9v2H1zM4.5 11h7v4h-7z"/></svg>
        <span>780.555.0163</span>
      </li>
      <li>
        <svg viewBox="0 0 16 16" aria-hidden="true"><path d="M1 4h14v9H1zM2.5 5l5.5 4 5.5-4z" fill-rule="evenodd"/></svg>
        <span>halya.dorosh@quillmail.example</span>
      </li>
    </ul>

    <div class="address-block">
      <div>20517 - 87 Ave.</div>
      <div>Edmonton, AB, Canada. T6K 4N8</div>
      <div class="web">www.brovix.example</div>
    </div>
  </section>

  <section class="card card-back" aria-label="Business card back">
    <div class="brand">
      <span class="brand-mark"></span>
      <span class="brand-name">brovix</span>
    </div>
    <div class="back-web">www.brovix.example</div>
  </section>
</body>
</html>
```